Buch-/eBook-Cover zum Thema Geldmanagement
Mein Projekt wurde sehr gut umgesetzt. Genau so hatte ich mir mein Cover vorgestellt. Herzlichen Dank.
Zielgruppe
ich benötige ein Buch-Cover (Vorder- und Rückseite) für das Buch Der Weg zur ruhigen Vermögenspflege. Untertitel ist Seelenfrieden trifft Finanzplanung. Das genaue Format ist im Briefing hinterlegt
Aufgabenstellung
Schön wäre es, wenn das Cover hell gehalten wäre. Es soll hochwertig aussehen. Ich habe zwar eigenes Bild-Material angegeben, es können jedoch auch andere Vorschläge kommen.

```html
<!DOCTYPE html>
<html lang="de">
<head>
<meta charset="utf-8">
<title>Der Weg zur ruhigen Vermögenspflege – Cover</title>
<link rel="stylesheet" href="https://fonts.googleapis.com/css2?family=Oswald:wght@500;700&family=Roboto+Condensed:wght@400&family=Roboto:wght@400&display=swap">
<style>
  :root {
    --gold-dark: #a8691a;
    --gold: #d99a2b;
    --gold-light: #f3b63c;
    --navy: #1b2452;
    --navy-deep: #141a38;
    --paper: #f3f3f4;
    --paper-edge: #e6e6e8;
    --stone-light: #b9b8ae;
    --stone-dark: #7f7d74;
    --note: #d8894f;
    --white: #ffffff;
  }
  * { margin: 0; padding: 0; box-sizing: border-box; }
  html, body {
    width: 930px;
    height: 1200px;
    overflow: hidden;
    background: var(--white);
  }
  .cover {
    position: relative;
    width: 930px;
    height: 1200px;
    background: linear-gradient(180deg, var(--paper) 0%, var(--white) 55%, var(--paper-edge) 100%);
    overflow: hidden;
  }
  .subtitle-band {
    height: 82px;
    background: linear-gradient(90deg, var(--gold-dark) 0%, var(--gold) 45%, var(--gold-dark) 100%);
    display: flex;
    align-items: center;
    justify-content: center;
  }
  .subtitle {
    font-family: "Roboto Condensed", sans-serif;
    font-weight: 400;
    font-size: 40px;
    letter-spacing: 0.5px;
    color: var(--white);
    text-transform: uppercase;
    white-space: nowrap;
  }
  .title {
    margin-top: 22px;
    text-align: center;
    font-family: "Oswald", sans-serif;
    font-weight: 700;
    text-transform: uppercase;
    line-height: 1;
    white-space: nowrap;
  }
  .title-line { display: block; }
  .title-lead {
    display: flex;
    align-items: center;
    justify-content: center;
    gap: 26px;
    font-size: 62px;
    color: var(--navy);
    letter-spacing: 1px;
  }
  .title-lead::before,
  .title-lead::after {
    content: "";
    width: 96px;
    height: 5px;
    background: var(--navy);
  }
  .title-gold {
    background: linear-gradient(180deg, var(--gold-light) 0%, var(--gold) 50%, var(--gold-dark) 100%);
    -webkit-background-clip: text;
    background-clip: text;
    color: transparent;
  }
  .title-mid { font-size: 124px; line-height: 1.08; margin-top: 2px; }
  .title-big {
    font-size: 168px;
    line-height: 1.14;
    margin-top: 10px;
    letter-spacing: -1px;
  }
  .title-close {
    font-size: 100px;
    color: var(--navy);
    margin-top: -4px;
    letter-spacing: 1px;
  }
  .cover-image {
    position: absolute;
    left: 50%;
    top: 648px;
    transform: translateX(-50%);
    width: 360px;
    height: 344px;
  }
  .footer-rule {
    position: absolute;
    left: 0;
    top: 994px;
    width: 100%;
    height: 8px;
    background: linear-gradient(90deg, var(--gold-dark), var(--gold-light), var(--gold-dark));
  }
  .author-band {
    position: absolute;
    left: 0;
    top: 1002px;
    width: 100%;
    height: 198px;
    background: linear-gradient(180deg, var(--navy) 0%, var(--navy-deep) 100%);
    display: flex;
    justify-content: center;
    padding-top: 52px;
  }
  .author {
    font-family: "Roboto", sans-serif;
    font-weight: 400;
    font-size: 36px;
    letter-spacing: 5px;
    color: var(--white);
    text-transform: uppercase;
  }
</style>
</head>
<body>
  <main class="cover">
    <header class="subtitle-band">
      <p class="subtitle">Seelenfrieden trifft Finanzplanung</p>
    </header>

    <h1 class="title">
      <span class="title-line title-lead">Der Weg zur</span>
      <span class="title-line title-gold title-mid">Ruhigen</span>
      <span class="title-line title-gold title-big">Vermögens</span>
      <span class="title-line title-close">pflege</span>
    </h1>

    <svg class="cover-image" viewBox="0 0 360 344" role="img" aria-label="Foto: gestapelte Kieselsteine mit einem gerollten Geldschein obenauf">
      <defs>
        <linearGradient id="stack-tone" x1="0" y1="0" x2="0" y2="1">
          <stop offset="0" stop-color="var(--note)" stop-opacity="0.85"/>
          <stop offset="0.3" stop-color="var(--stone-light)"/>
          <stop offset="1" stop-color="var(--stone-dark)"/>
        </linearGradient>
      </defs>
      <rect x="0" y="0" width="360" height="344" rx="24" fill="url(#stack-tone)" opacity="0.55"/>
    </svg>

    <div class="footer-rule"></div>
    <footer class="author-band">
      <p class="author">Author Name</p>
    </footer>
  </main>
</body>
</html>
```